Web Design Project for a Software & Consulting Company

We have just completed a recent ArtHerdly project for a new logo (see attached).
As the next stage of our rebranding we now require a website re-design to complement the new logo.
Our current site, http://www.corvinsoft.example was built in-house and does not come across as professional as we would like. We supply software and associated services to some of the world’s largest oil companies and we need our site to reflect that level of client.
We will also be posting another design project for brochures, PowerPoint slides and other materials very soon.
We would like designs for…
Home page
Product page
• TZQ
• BLV
• PNJ
Services
News page
About Us page
Contact Us page
Page for mobile devices that gives basic company and product information
Currently the site is small but we intend to increase content to include white papers etc. this should be taken into account when designing the navigation therefore we would prefer navigation through styled text links rather than images.
Colour schemes should broadly be taken from our new logo, where the dark blue and dark green from the left and right sides of the logo are the main colours, but other, brighter accent colours can be used to highlight sections or content.
Dark Blue = C:88, M:55, Y:44, K:28
Dark Green = C:87, M:53, Y:50, K:50
NB: Don’t use the logo on our current site, make sure you use the one attached.
We would prefer the final file format to be a layered PSD.
The site should be clean and professional and communicate the following...
• That we have a great depth and breadth of knowledge about our customers’ business, enabling us to deliver the best systems and solutions.
• That we are a leading provider of cost estimation and control solutions to the oil and gas industry.
• The benefits of our software and consulting services.
• Show that we deliver outstanding customer service and value with a very high level of professionalism
• The site should have no Flash and be able to self-adjust to fit any screen size.
Things to avoid …
• Obvious and clichéd oil industry imagery, no oil rigs
• Cartoon style graphics
Our Background
We are an integrated software and consulting organization specialising in the drilling side of the oil and gas industry. Simply put our software helps companies better understand, predict and communicate the cost of drilling wells.
We have 3 software products and a consulting offering consisting of…
• TZQ - Probabilistic time and cost software
• BLV – Cost tracking and reporting software
• PNJ – (currently known as DrillSavant) – Lessons learned software
• Consulting services
Our systems are in use in over 30 countries with a broad range of clients including: GN, Marovel, Dunt, Koruna, VELO Sirkami, FALUMI and Quintex.
Our current site can be found at www.corvinsoft.example
Our main competitors are
• http://www.drovanic.example/
• http://www.sumbrask.example/
• http://www.kve.example/services/software-solutions/p1-
Our depth of drilling knowledge, quality of software and collaboration with clients differentiate us form the competition.
We strive for very high levels of customer service.
We look forward to receiving your designs!
Updates
Thanks to all the designers who have submitted a design, we appreciate the effort.
We will do our best to give individual feedback on each design but given that many are quite similar we thought we would give some general feedback first.
Nearly all the designs submitted so far have been slight variations on…
-
Top Menu
-
Scrolling Photo Banner
-
4 Columns
-
Body
-
Deep Footer
These designs are well executed but they are basically the same layout as our existing site and while there is nothing inherently wrong with this layout we would like to see some designs that are a bit more innovative and different. We don’t really want just a polished version of our current site.
Thanks again,
CVS
Thanks to everyone who has submitted a design, the response has been great.
We are close to making a decision so if you are intending to submit a design please do it soon, the deadline is only a few days away.
Thanks again.
CVS
Target Market(s)
Mid to high level executives
Industry/Entity Type
Oil And Gas
Look and feel

```html
<!DOCTYPE html>
<html lang="en">
<head>
<meta charset="utf-8">
<title>Corvinsoft – TZQ</title>
<link rel="stylesheet" href="https://fonts.googleapis.com/css2?family=PT+Sans:wght@400;700&family=PT+Sans+Narrow&family=Arimo:wght@400;700&display=swap">
<style>
:root{
  --ink:#333;
  --teal:#1d5566;
  --teal-deep:#174758;
  --nav-active:#1f5a6a;
  --link:#0a89ad;
  --rule:#cfcfcf;
  --footer-a:#24596b;
  --footer-b:#1a4a5b;
  --footer-text:#e6eef1;
  --white:#fff;
}
*{margin:0;padding:0;box-sizing:border-box}
html,body{width:952px;height:1200px;overflow:hidden;background:var(--white)}
body{position:relative;font-family:"Arimo",Arial,sans-serif;color:var(--ink)}
.abs{position:absolute}

/* header */
.brand{left:116px;top:38px;display:flex;align-items:center;gap:10px}
.brand-mark{width:34px;height:34px;border-radius:50%;background:var(--teal)}
.brand-name{font-family:"PT Sans",sans-serif;font-weight:700;font-size:22px;color:var(--teal);letter-spacing:.5px}
.nav{list-style:none}
.nav li{position:absolute;top:55px;height:25px;line-height:25px;font-family:"PT Sans Narrow",sans-serif;font-size:13px;color:#222;white-space:nowrap}
.nav li.active{background:var(--nav-active);color:var(--white);border-radius:3px;padding:0 8px;border:1px solid #103845}

/* hero */
.hero{left:94px;top:129px;width:762px;height:238px;overflow:hidden;
  background:linear-gradient(100deg,#dfe9ef 0%,#c9d7df 30%,#a9bcc7 55%,#6f8ea1 75%,#1f3e6e 90%,#16306a 100%)}
.hero-caption{position:absolute;left:0;top:164px;width:762px;height:52px;background:rgba(17,62,78,.88);
  font-family:"PT Sans",sans-serif;font-weight:700;font-size:21px;color:var(--white);line-height:52px;padding-left:28px}

/* intro */
.intro-icon{left:94px;top:400px;width:32px;height:28px;border-radius:3px;background:linear-gradient(#cfe3ef,#7fa6bd)}
.intro-title{left:144px;top:405px;font-family:"PT Sans",sans-serif;font-size:16px;color:var(--teal)}
.copy{font-size:10px;line-height:14px;color:#444}
.intro-lead{left:96px;top:448px;width:740px}
.intro-body{left:96px;top:482px;width:740px}
.intro-list{left:96px;top:553px;list-style:none}
.intro-list li{font-size:10px;line-height:18.5px;color:#444;padding-left:16px;position:relative}
.intro-list li::before{content:"";position:absolute;left:2px;top:7px;width:4px;height:4px;border-radius:50%;background:#333}

/* section heads */
.section-title{font-family:"PT Sans",sans-serif;font-size:16px;color:var(--teal)}
.section-rule{height:2px;background:var(--rule)}

/* features */
.feature-icon{width:34px;height:38px;border-radius:3px}
.feature-text{width:140px;font-size:9.5px;line-height:16px;color:#222}
.feature-text b{font-weight:700}
.read-more{font-size:9px;font-weight:700;color:var(--link);display:flex;align-items:center;gap:6px}
.read-more svg{flex:none}

/* product thumbs */
.thumb{width:82px;height:82px;border:1px solid #d6d6d6;background:#f2f2f2;padding:3px}
.thumb span{display:block;width:100%;height:100%}

/* footer */
.footer{left:94px;top:969px;width:762px;height:231px;background:linear-gradient(180deg,var(--footer-a),var(--footer-b));border:1px solid #164050}
.f-head{font-family:"PT Sans",sans-serif;font-size:12.5px;color:var(--white)}
.f-line{height:1px;background:#6f98a6}
.f-addr{font-family:"PT Sans",sans-serif;font-size:9.5px;line-height:13.6px;color:var(--footer-text)}
.badge{width:100px;height:40px;border-radius:4px;background:rgba(255,255,255,.18)}
.touch{font-family:"PT Sans",sans-serif;font-size:15px;color:var(--white)}
.field{left:672px;width:158px;background:var(--white);border:1px solid #9fb8c2;border-radius:2px;font-family:"PT Sans",sans-serif;font-size:10px;color:#333;padding:4px 8px}
.submit{left:779px;top:1134px;width:51px;height:20px;background:linear-gradient(#fff,#dcdcdc);border:1px solid #999;border-radius:2px;font-family:"PT Sans",sans-serif;font-size:8.5px;font-weight:700;text-align:center;line-height:18px;color:#222}
.f-copy{left:116px;top:1096px;width:520px;font-size:9.3px;line-height:11.7px;color:var(--footer-text)}
.f-bottom{left:94px;top:1167px;width:762px;height:1px;background:#123d4c}
.f-links{left:116px;top:1179px;font-family:"PT Sans",sans-serif;font-size:9px;color:var(--footer-text)}
.f-rights{left:718px;top:1179px;font-family:"PT Sans",sans-serif;font-size:9px;color:var(--footer-text)}
</style>
</head>
<body>

<header>
  <div class="abs brand"><span class="brand-mark"></span><span class="brand-name">CORVINSOFT</span></div>
  <ul class="nav">
    <li style="left:422px">HOME</li>
    <li class="active" style="left:478px">PRODUCTS</li>
    <li style="left:571px">ABOUT US</li>
    <li style="left:654px">NEWS</li>
    <li style="left:716px">SOLUTIONS</li>
    <li style="left:802px">CONTACT US</li>
  </ul>
</header>

<section class="abs hero" role="img" aria-label="Photo of hands typing on a laptop keyboard in an office">
  <div class="hero-caption">TZQ - Probabilistic time and cost software</div>
</section>

<section>
  <div class="abs intro-icon" role="img" aria-label="Desktop computer icon"></div>
  <h1 class="abs intro-title">THE BEST TIME AND COST PROBABILISTIC SOFTWARE</h1>
  <p class="abs copy intro-lead">Lorem ipsum dolor sit amet, consectetur adipiscing elit. Ut eget augue orci. Quisque accumsan vestibulum massa ac vestibulum.</p>
  <p class="abs copy intro-body">Praesent at est neque. Vivamus felis augue, pharetra molestie pretium non, rutrum sed lorem. Suspendisse eu metus eu nibh fermentum cursus. Etiam in diam risus. Ut pellentesque felis mauris, nec dapibus purus. Fusce id mauris odio. Mauris facilisis ipsum ac nunc vestibulum facilisis. Maecenas vel scelerisque elit. Mauris interdum mauris ut orci tempus cursus. Nam at erat sed nulla consectetur dignissim. Nullam urna leo, congue a lobortis id, elementum et orci. In sed lacinia dolor. Nulla fermentum nisl tellus.</p>
  <ul class="abs intro-list">
    <li>Morbi ac ultricies justo.</li>
    <li>Integer id nisi vitae lacus fringilla blandit at non orci.</li>
    <li>Fusce non lacus et dui vulputate laoreet.</li>
  </ul>
</section>

<section>
  <h2 class="abs section-title" style="left:114px;top:636px">MAIN FEATURES</h2>
  <div class="abs section-rule" style="left:96px;top:667px;width:430px"></div>

  <div class="abs feature-icon" style="left:110px;top:692px;background:linear-gradient(90deg,#3c6f8f,#47b6e6)" role="img" aria-label="Book icon"></div>
  <p class="abs feature-text" style="left:158px;top:690px"><b>The point of using Lorem Ipsum</b> is that it has a more-or-less normal distribution of letters, as opposed to using 'Content here, content here', making it look like readable English.</p>
  <a class="abs read-more" style="left:222px;top:804px"><svg width="10" height="10" viewBox="0 0 10 10"><circle cx="5" cy="5" r="5" fill="#444"/><path d="M5 2.5v5M2.5 5h5" stroke="#fff" stroke-width="1.4"/></svg>Read More</a>

  <div class="abs feature-icon" style="left:322px;top:690px;width:38px;height:42px;background:linear-gradient(#e09a55,#b8662a)" role="img" aria-label="Open box icon"></div>
  <p class="abs feature-text" style="left:376px;top:690px"><b>Many desktop</b> publishing packages and web page editors now use Lorem Ipsum as their default model text, and a search for 'lorem ipsum' will uncover many web sites still in their infancy.</p>
  <a class="abs read-more" style="left:447px;top:804px"><svg width="10" height="10" viewBox="0 0 10 10"><circle cx="5" cy="5" r="5" fill="#444"/><path d="M5 2.5v5M2.5 5h5" stroke="#fff" stroke-width="1.4"/></svg>Read More</a>

  <div class="abs feature-icon" style="left:108px;top:838px;width:32px;background:linear-gradient(#f3f0ea,#d9cbb4);border:2px solid #c98a4a" role="img" aria-label="Clipboard icon"></div>
  <p class="abs feature-text" style="left:158px;top:836px"><b>Various versions</b> have evolved over the years, sometimes by accident, sometimes on purpose (injected humour and the like).</p>
  <a class="abs read-more" style="left:222px;top:918px"><svg width="10" height="10" viewBox="0 0 10 10"><circle cx="5" cy="5" r="5" fill="#444"/><path d="M5 2.5v5M2.5 5h5" stroke="#fff" stroke-width="1.4"/></svg>Read More</a>

  <svg class="abs" style="left:326px;top:838px" width="36" height="36" viewBox="0 0 36 36" role="img" aria-label="Help icon">
    <circle cx="18" cy="18" r="16" fill="#3a58a8" stroke="#c9d2e8" stroke-width="2"/>
    <path d="M13 14a5 5 0 1 1 7 4.5c-1.5.8-2 1.6-2 3.5" fill="none" stroke="#fff" stroke-width="3" stroke-linecap="round"/>
    <circle cx="18" cy="26.5" r="1.9" fill="#fff"/>
  </svg>
  <p class="abs feature-text" style="left:376px;top:836px"><b>Contrary to popular</b> belief, Lorem Ipsum is not simply random text. It has roots in a piece of classical Latin literature from 45 BC.</p>
  <a class="abs read-more" style="left:445px;top:918px"><svg width="10" height="10" viewBox="0 0 10 10"><circle cx="5" cy="5" r="5" fill="#444"/><path d="M5 2.5v5M2.5 5h5" stroke="#fff" stroke-width="1.4"/></svg>Read More</a>
</section>

<section>
  <h2 class="abs section-title" style="left:571px;top:636px">SOFTWARE FEATURES</h2>
  <div class="abs section-rule" style="left:549px;top:667px;width:306px"></div>

  <div class="abs thumb" style="left:570px;top:691px"><span role="img" aria-label="Software screenshot: actual vs budget chart" style="background:linear-gradient(#f4c43a 0%,#f4c43a 18%,#e9eef3 18%,#c9d6e3 100%)"></span></div>
  <div class="abs thumb" style="left:658px;top:691px"><span role="img" aria-label="Software screenshot: bar chart with gauges" style="background:linear-gradient(#f7f9fb,#d8e2ea)"></span></div>
  <div class="abs thumb" style="left:746px;top:691px"><span role="img" aria-label="Software screenshot: 3D bar chart report" style="background:linear-gradient(#e9c34c 0%,#e9c34c 10%,#eef2f4 10%,#d6dee4 100%)"></span></div>
  <div class="abs thumb" style="left:570px;top:780px"><span role="img" aria-label="Software screenshot: forecast revenue gauge" style="background:linear-gradient(120deg,#eef3f7,#9db7c9)"></span></div>
  <div class="abs thumb" style="left:658px;top:780px"><span role="img" aria-label="Software screenshot: dashboard with column chart" style="background:linear-gradient(120deg,#e8eef4,#5f7fb0)"></span></div>
  <div class="abs thumb" style="left:746px;top:780px"><span role="img" aria-label="Software screenshot: green and blue column chart" style="background:linear-gradient(#f3f6f2,#b9d3a8)"></span></div>

  <a class="abs read-more" style="left:738px;top:877px"><svg width="10" height="10" viewBox="0 0 10 10"><circle cx="5" cy="5" r="5" fill="#444"/><path d="M5 2.5v5M2.5 5h5" stroke="#fff" stroke-width="1.4"/></svg>view all products</a>
</section>

<footer>
  <div class="abs footer"></div>

  <h3 class="abs f-head" style="left:118px;top:987px">EUROPE</h3>
  <div class="abs f-line" style="left:118px;top:1005px;width:117px"></div>
  <p class="abs f-addr" style="left:118px;top:1010px">18 Harlow Row<br>Dunmere, DX4 2KL<br>Phone:+44(0)1632 960417<br>Email:eu@corvinsoft.example</p>

  <h3 class="abs f-head" style="left:278px;top:985px">NORTH AMERICA</h3>
  <div class="abs f-line" style="left:278px;top:1005px;width:117px"></div>
  <p class="abs f-addr" style="left:278px;top:1010px">4100 Lantern Park Dr, Suite 210<br>Brackley, TX 77099<br>Phone:(555) 014 2290<br>Email:us@corvinsoft.example</p>

  <h3 class="abs f-head" style="left:454px;top:985px">OUR GOLD BUSINESS PARTNER</h3>
  <div class="abs f-line" style="left:454px;top:1005px;width:179px"></div>
  <div class="abs badge" style="left:492px;top:1020px" role="img" aria-label="Partner badge"></div>

  <h3 class="abs touch" style="left:672px;top:981px">Get in touch</h3>
  <div class="abs f-line" style="left:672px;top:1006px;width:145px;background:linear-gradient(90deg,#4fb6d6,transparent)"></div>
  <div class="abs field" style="top:1020px;height:21px">Name</div>
  <div class="abs field" style="top:1048px;height:21px">E-mail</div>
  <div class="abs field" style="top:1076px;height:50px">Message</div>
  <div class="abs submit">SUBMIT</div>

  <div class="abs f-line" style="left:118px;top:1084px;width:526px;background:#4f7f8f"></div>
  <p class="abs f-copy">Lorem ipsum dolor sit amet, consectetur adipiscing elit. Donec semper nisl eget ante vehicula at viverra est porta. Morbi eleifend, turpis eget vehicula porta, leo velit facilisis justo, quis vehicula velit erat nec est. Pellentesque habitant morbi tristique senectus et netus et malesuada fames ac turpis egestas. Pellentesque consequat est vel metus luctus commodo. In hac habitasse platea dictumst. Suspendisse justo ipsum,</p>

  <div class="abs f-bottom"></div>
  <p class="abs f-links">Privacy Policy &nbsp;&nbsp;|&nbsp;&nbsp; Terms &amp; Conditions</p>
  <p class="abs f-rights">© Copyrights 2012 Corvinsoft</p>
</footer>

</body>
</html>
```